Grafik/Logo für ein Schulungszertifikat DIN A4
Zielgruppe
Es soll nach einer Schulung für Social Media und Online Marketing für Unternehmer und Selbstständige ein Zertifikat auf dickerem Papier ausgehändigt werden.
Auf dieses sollen die Teilnehmer stolz sein ;-) und im Büro oder im Geschäft aufhängen wollen.
Das Logo des Zertifikates darf anschließend auch alleinstehend auf der Homepage der Unternehmensseiten von Teilnehmern verwendet werden dürfen.
Es soll eine Gemeinschaft symbolisiert werden. Denn bei dieser Schulung schulen Unternehmer aus dem Bereich Onlinemarketing andere Unternehmer aus unterschiedlichsten Branchen und Bereichen. Eben aus allen, in denen Onlinemarketing und Social Media sinnvoll eingesetzt werden kann.
Die Inhalte können Sie dem beigefügten Dokument entnehmen.
Aufgabenstellung
Es werden benötigt:
1. Ein Logo/Zertifikatssiegel (auffälig sein und ins Auge fallen, ob online oder wenn das an der Wand hängt, oder als Autoaufkleber genutzt wird)
2. Layout für das DIN A 4 Zertifikat mit dem Zertifikatssiegel

```html
<!DOCTYPE html>
<html lang="de">
<head>
<meta charset="utf-8">
<title>Zertifikat – Social Media und Online Marketing</title>
<link rel="stylesheet" href="https://fonts.googleapis.com/css2?family=Cinzel:wght@400;600;700&display=swap">
<style>
  :root {
    --paper: #d9eed9;
    --ink: #111111;
    --green: #3a9a44;
    --green-light: #57b94b;
    --green-dark: #0c5e30;
    --gold-light: #fbf3a8;
    --gold-mid: #c9a14a;
    --gold-dark: #6e4f0c;
  }
  html, body {
    margin: 0;
    padding: 0;
    overflow: hidden;
    background: var(--paper);
  }
  .certificate {
    position: relative;
    width: 848px;
    height: 1200px;
    overflow: hidden;
    background: var(--paper);
    color: var(--ink);
    font-family: "Cinzel", "Times New Roman", serif;
    font-weight: 600;
  }
  .certificate p { margin: 0; }
  .title {
    position: absolute;
    left: 54px;
    top: 84px;
    margin: 0;
    font-size: 82px;
    font-weight: 700;
    letter-spacing: 2px;
    line-height: 1;
  }
  .text {
    position: absolute;
    left: 49px;
    font-size: 24px;
    line-height: 27px;
    white-space: nowrap;
  }
  .salutation { top: 240px; font-size: 26px; }
  .name-line {
    position: absolute;
    left: 48px;
    top: 307px;
    width: 311px;
    border-top: 1.5px solid var(--ink);
  }
  .success { top: 353px; line-height: 30px; font-size: 25px; }
  .institute-logo {
    position: absolute;
    left: 167px;
    top: 434px;
    width: 200px;
    height: 200px;
    border-radius: 50%;
    background: var(--green);
    display: flex;
    align-items: center;
    justify-content: center;
    text-align: center;
    font-size: 25px;
    line-height: 29px;
  }
  .attendance { top: 654px; }
  .attendance .blank {
    display: inline-block;
    width: 156px;
    border-bottom: 1.5px solid var(--ink);
    margin: 0 12px 0 14px;
  }
  .focus-heading { top: 788px; }
  .topics {
    position: absolute;
    left: 100px;
    top: 842px;
    margin: 0;
    padding: 0;
    list-style: none;
    font-size: 19px;
    line-height: 24.5px;
    white-space: nowrap;
  }
  .topics li::before { content: "· "; }
  .topics .more { padding-left: 10px; }
  .topics .more::before { content: ""; }
  .signature-line {
    position: absolute;
    left: 48px;
    width: 227px;
    border-top: 1px solid var(--ink);
  }
  .signature-label {
    position: absolute;
    left: 48px;
    width: 227px;
    text-align: center;
    font-size: 19.5px;
  }
  .lecturer-line { top: 1068px; }
  .lecturer-label { top: 1078px; }
  .director-line { top: 1142px; }
  .director-label { top: 1153px; }
  .issued-label {
    position: absolute;
    left: 351px;
    top: 1153px;
    font-size: 19.5px;
  }
  .issued-line {
    position: absolute;
    left: 545px;
    top: 1175px;
    width: 127px;
    border-top: 1px solid var(--ink);
  }
  .ribbon {
    position: absolute;
    left: 602px;
    top: 20px;
    width: 145px;
    height: 870px;
    background: linear-gradient(to bottom, var(--gold-light) 0%, var(--gold-mid) 45%, var(--gold-dark) 100%);
  }
  .ribbon-band {
    position: absolute;
    left: 14px;
    top: 13px;
    width: 116px;
    height: 857px;
    background: linear-gradient(to bottom, var(--green-light) 0%, #2f8f45 40%, var(--green-dark) 75%, #1a7a3a 100%);
  }
  .ribbon-title {
    position: absolute;
    left: -272px;
    top: 272px;
    width: 660px;
    height: 116px;
    transform: rotate(-90deg);
    box-sizing: border-box;
    padding: 14px 0 0 2px;
    margin: 0;
    font-size: 29px;
    line-height: 37px;
    font-weight: 600;
    color: var(--ink);
    white-space: nowrap;
  }
  .seal-mark {
    position: absolute;
    left: 577px;
    top: 852px;
    width: 200px;
    height: 200px;
    border-radius: 50%;
    background: var(--green);
  }
  .seal-name {
    position: absolute;
    left: 537px;
    top: 1062px;
    width: 280px;
    text-align: center;
    font-size: 26px;
    font-weight: 700;
    color: var(--green-dark);
  }
</style>
</head>
<body>
<main class="certificate">
  <h1 class="title">Zertifikat</h1>

  <p class="text salutation">Herr/Frau</p>
  <div class="name-line"></div>

  <p class="text success">hat erfolgreich am Seminar<br>teilgenommen!</p>

  <div class="institute-logo">Logo<br>Bildungs-<br>institut</div>

  <p class="text attendance">
    Wir bescheinigen die Teilnahme<br>
    vom<span class="blank"></span>bis zum<span class="blank"></span><br>
    in den Räumlichkeiten der 'Name Institut'<br>
    PLZ/ Ort
  </p>

  <p class="text focus-heading">Schwerpunkte der Wissensvermittlung:</p>
  <ul class="topics">
    <li>Erfolgreich im Web kommunizieren</li>
    <li>Suchmaschinenoptimierung</li>
    <li>Blogredaktion</li>
    <li>Kontaktring</li>
    <li>Kurzfunk und Linkwelt</li>
    <li>Fotoliga Marketing</li>
    <li class="more">u.v.m.</li>
  </ul>

  <div class="signature-line lecturer-line"></div>
  <p class="signature-label lecturer-label">Dozent Institut</p>
  <div class="signature-line director-line"></div>
  <p class="signature-label director-label">Direktion Institut</p>

  <p class="issued-label">Ausgestellt am:</p>
  <div class="issued-line"></div>

  <div class="ribbon">
    <div class="ribbon-band">
      <h2 class="ribbon-title">Social Media – und Online Marketing<br>für Selbstständige</h2>
    </div>
  </div>

  <div class="seal-mark"></div>
  <p class="seal-name">Profiwissen</p>
</main>
</body>
</html>
```